KBT Business Cards

We require business cards for our business. We would like a matte black back to the card, with our logo centred in the middle. The front side of the card is open to design.

Target Market(s)

Clients looking for legal services (professional)

Industry/Entity Type

Legal

Contact Information for Business Card

Doran Kelbrath
Partner
Mobile: 0461 738 524
Email: doran@kbtlaw.co
Website: www.kbtlaw.co
Level 3, 118 Wendmore Street
Sydney NSW 2000

Font styles to use
Other font styles liked:
• Avenir

Colors
f04a50
ffffff
1b1b1b

Requirements
Must have
• Black back with logo included in the centre of the card.
• Our font is Avenir.

```html
<!DOCTYPE html>
<html lang="en">
<head>
<meta charset="utf-8">
<title>KBT Business Cards</title>
<link rel="stylesheet" href="https://fonts.googleapis.com/css2?family=Roboto:wght@400;500;700&display=swap">
<style>
  :root {
    --backdrop: #dcdcdc;
    --card-white: #ffffff;
    --card-black: #231f20;
    --crimson: #cf2146;
    --crimson-deep: #a51e38;
    --ink: #231f20;
    --body-grey: #555555;
  }
  * { margin: 0; padding: 0; box-sizing: border-box; }
  html, body {
    width: 1125px;
    height: 1200px;
    overflow: hidden;
    background: var(--backdrop);
    font-family: "Roboto", Arial, sans-serif;
  }
  .canvas {
    position: relative;
    width: 1125px;
    height: 1200px;
  }
  .card {
    position: absolute;
    left: 171px;
    width: 826px;
    height: 471px;
    overflow: hidden;
  }
  .card--front { top: 106px; background: var(--card-white); }
  .card--back  { top: 639px; background: var(--card-black); }

  .accent-field {
    position: absolute;
    top: 0;
    height: 100%;
  }
  .accent-field--left {
    left: 0;
    width: 230px;
    background: linear-gradient(135deg, var(--crimson), var(--crimson-deep));
  }
  .accent-field--right {
    right: 0;
    width: 230px;
    background: var(--card-black);
  }

  .contact {
    position: absolute;
    left: 0;
    right: 0;
    top: 134px;
    text-align: center;
  }
  .contact__name {
    font-size: 30px;
    font-weight: 500;
    color: var(--crimson);
    letter-spacing: 0.3px;
    line-height: 1;
  }
  .contact__role {
    margin-top: 6px;
    font-size: 20px;
    font-weight: 500;
    color: var(--ink);
    letter-spacing: 0.5px;
    line-height: 1;
  }
  .contact__address {
    margin-top: 18px;
    font-size: 19.5px;
    color: var(--body-grey);
    line-height: 25px;
  }
  .contact__lines {
    margin-top: 9px;
    font-size: 19.5px;
    color: var(--body-grey);
    line-height: 27px;
  }

  .brand {
    position: absolute;
    left: 0;
    right: 0;
    top: 0;
    bottom: 0;
    display: flex;
    align-items: center;
    justify-content: center;
    gap: 36px;
  }
  .brand__square {
    width: 64px;
    height: 64px;
    background: var(--crimson);
  }
  .brand__name {
    font-size: 41px;
    font-weight: 500;
    color: var(--card-white);
    line-height: 44px;
    letter-spacing: 0.5px;
  }
</style>
</head>
<body>
  <main class="canvas">
    <section class="card card--front" aria-label="Business card front">
      <div class="accent-field accent-field--left" role="img" aria-label="Crimson geometric pattern area"></div>
      <div class="accent-field accent-field--right" role="img" aria-label="Black geometric pattern area"></div>
      <div class="contact">
        <p class="contact__name">DORAN KELBRATH</p>
        <p class="contact__role">PARTNER</p>
        <p class="contact__address">Level 3, 118 Wendmore Street<br>Sydney NSW 2000</p>
        <p class="contact__lines">0461 738 524 | doran@kbtlaw.co<br>www.kbtlaw.co</p>
      </div>
    </section>

    <section class="card card--back" aria-label="Business card back">
      <div class="brand">
        <div class="brand__square"></div>
        <p class="brand__name">KELBRATH<br>BARROW<br>THORNE</p>
      </div>
    </section>
  </main>
</body>
</html>
```